VOR Exterior Coatings

double sided. the front i want the name of the business each word on a new line with the VOR being bigger. id like teal, black and white colors. the back i want my contact info. Flat, no gloss. Something professional and I want to feel the letters bump put of the card. if possible maybe a paint sprayer in corner. not a car paint spray. (no tank on top of gun)
no vehicle paint sprayers. that means no tank on top of the gun. doesn't have to have a sprayer. black/dark background on the front. white back ground on back with info

```html
<!DOCTYPE html>
<html lang="en">
<head>
<meta charset="utf-8">
<title>VOR Exterior Coatings – Business Card</title>
<link rel="stylesheet" href="https://fonts.googleapis.com/css2?family=Oswald:wght@500&family=Lato:wght@400;700&display=swap">
<style>
  :root {
    --teal: #0a8a8a;
    --ink: #1f1f1f;
    --text-grey: #4a4a4a;
    --paper: #f7f7f7;
    --stage: #e6e4e1;
    --card-dark-top: #303030;
    --card-dark-bottom: #222222;
    --deboss: #3e3e3e;
  }
  * { box-sizing: border-box; margin: 0; padding: 0; }
  html, body {
    width: 1200px; height: 1200px; overflow: hidden;
    background: var(--stage);
  }
  .canvas { position: relative; width: 1200px; height: 1200px; }

  .card {
    position: absolute; left: 150px; width: 900px; height: 514px;
    overflow: hidden;
  }
  .card--front { top: 56px; background: var(--paper); }
  .card--back {
    top: 630px;
    background: linear-gradient(180deg, var(--card-dark-top), var(--card-dark-bottom));
  }

  /* Name band */
  .name-band {
    position: absolute; left: 0; top: 92px; width: 331px; height: 86px;
    background: var(--teal);
    clip-path: polygon(0 0, 274px 0, 331px 100%, 0 100%);
  }
  .name-band__name {
    position: absolute; left: 46px; top: 12px;
    font-family: "Oswald", sans-serif; font-weight: 500;
    font-size: 37px; line-height: 1; color: #fff; letter-spacing: 0.2px;
  }
  .name-band__title {
    position: absolute; left: 47px; top: 51px;
    font-family: "Lato", sans-serif; font-size: 22px; line-height: 1; color: #fff;
  }

  /* Business name */
  .brand {
    position: absolute; right: 58px; top: 48px;
    text-align: center;
    font-family: "Lato", sans-serif; font-weight: 700;
  }
  .brand__name {
    display: block; font-size: 124px; line-height: 1; color: var(--teal);
  }
  .brand__tagline {
    display: block; font-size: 22px; line-height: 1; margin-top: 2px;
    color: var(--ink); letter-spacing: 0.4px;
  }

  /* Contacts */
  .contacts {
    position: absolute; left: 48px; top: 290px; list-style: none;
    font-family: "Lato", sans-serif; font-size: 21px; color: var(--text-grey);
  }
  .contacts li { display: flex; align-items: center; height: 26.4px; }
  .contacts svg { width: 20px; height: 20px; margin-right: 13px; fill: var(--teal); flex: none; }

  /* Address bar */
  .address-bar {
    position: absolute; left: 0; top: 438px; width: 100%; height: 34px;
    background: var(--ink); color: #fff;
    font-family: "Lato", sans-serif; font-size: 21px; line-height: 34px;
    padding-left: 45px;
  }

  /* Back */
  .brand--back {
    right: auto; left: 50%; top: 160px; transform: translateX(-50%);
  }
  .brand--back .brand__name { font-size: 180px; color: var(--deboss); }
  .brand--back .brand__tagline { font-size: 32px; margin-top: 0; color: var(--deboss); }
</style>
</head>
<body>
<div class="canvas">

  <section class="card card--front">
    <div class="name-band">
      <div class="name-band__name">DANIEL BROOKS</div>
      <div class="name-band__title">Founder &amp; CEO</div>
    </div>

    <div class="brand">
      <span class="brand__name">VOR</span>
      <span class="brand__tagline">EXTERIOR COATINGS</span>
    </div>

    <ul class="contacts">
      <li>
        <svg viewBox="0 0 24 24"><path d="M6.6 10.8a15.1 15.1 0 0 0 6.6 6.6l2.2-2.2a1 1 0 0 1 1-.25 11.4 11.4 0 0 0 3.6.57 1 1 0 0 1 1 1V20a1 1 0 0 1-1 1A17 17 0 0 1 3 4a1 1 0 0 1 1-1h3.5a1 1 0 0 1 1 1c0 1.25.2 2.45.57 3.57a1 1 0 0 1-.25 1z"/></svg>
        555-210-4817
      </li>
      <li>
        <svg viewBox="0 0 24 24"><path d="M7 1h10a2 2 0 0 1 2 2v18a2 2 0 0 1-2 2H7a2 2 0 0 1-2-2V3a2 2 0 0 1 2-2zm0 3v14h10V4zm5 15.5a1.2 1.2 0 1 0 0 2.4 1.2 1.2 0 0 0 0-2.4z"/></svg>
        555-362-9045
      </li>
      <li>
        <svg viewBox="0 0 24 24"><path d="M6 2h9l3 3v4H6zM3 10h18a2 2 0 0 1 2 2v6h-4v4H5v-4H1v-6a2 2 0 0 1 2-2zm4 7v3h10v-3z"/></svg>
        555-784-1296
      </li>
      <li>
        <svg viewBox="0 0 24 24"><path d="M2 5h20v14H2zm2 2v.4l8 5.2 8-5.2V7zm0 2.8V17h16V9.8l-8 5.2z"/></svg>
        info@vorexteriorcoatings.com
      </li>
      <li>
        <svg viewBox="0 0 24 24"><path d="M12 2a10 10 0 1 0 0 20 10 10 0 0 0 0-20zm-1 17.9A8 8 0 0 1 4.2 10l4.8 4.8v1a2 2 0 0 0 2 2zm6.9-2.5A2 2 0 0 0 16 16h-1v-3a1 1 0 0 0-1-1H8v-2h2a1 1 0 0 0 1-1V7h2a2 2 0 0 0 2-2v-.4a8 8 0 0 1 2.9 12.8z"/></svg>
        www.vorexteriorcoatings.com
      </li>
    </ul>

    <div class="address-bar">1420 Birchwood Lane, Anchorage, Alaska 99508</div>
  </section>

  <section class="card card--back">
    <div class="brand brand--back">
      <span class="brand__name">VOR</span>
      <span class="brand__tagline">EXTERIOR COATINGS</span>
    </div>
  </section>

</div>
</body>
</html>
```